Demolition Company Billboard Design 13 feet wide 15 feet high

This is my first billboard on a busy road. I want it to be professional but with some eye catching flair that matches by business which is a demoltion business and also list my services. My company slogan is also

"watch kessel clear the lot"

Target Market(s)

Home Ownerd and General Construction Companies

Industry/Entity Type

construction

Colors
0054AA
0677BA
7BADD7
CADEEF
E8F1F8

Requirements
Must have
• My services listed in the pictures my website and my phone number

```html
<!DOCTYPE html>
<html lang="en">
<head>
<meta charset="utf-8">
<title>Kessel Demolition Billboard</title>
<link rel="stylesheet" href="https://fonts.googleapis.com/css2?family=Bebas+Neue&family=Oswald:wght@300;600&display=swap">
<style>
  :root {
    --navy: #134a8f;
    --blue: #1155a6;
    --bracket-top: #0d6bbd;
    --bracket-bottom: #0a4f9c;
    --bar: #47474a;
    --ink: #111a33;
    --phone: #1456a6;
    --white: #ffffff;
    --photo-brick: #9a4a3a;
    --photo-sky: #c9d7e6;
    --photo-debris: #8a7a62;
  }
  * { margin: 0; padding: 0; box-sizing: border-box; }
  html, body { width: 1040px; height: 1200px; overflow: hidden; background: var(--white); }
  .billboard { position: relative; width: 1040px; height: 1200px; background: var(--white); overflow: hidden; }
  .shapes { position: absolute; inset: 0; }

  .brand {
    position: absolute; left: 60px; top: 82px;
    display: flex; align-items: center; gap: 14px;
    font-family: "Bebas Neue", sans-serif; font-size: 92px; line-height: 1;
    color: var(--bar); letter-spacing: 4px;
  }
  .brand-mark { width: 30px; height: 30px; background: var(--navy); }

  .headline {
    position: absolute; right: 63px; top: 40px;
    text-align: right; color: var(--white);
    font-family: "Bebas Neue", sans-serif; line-height: 0.92;
  }
  .headline .line { display: block; }
  .headline .lead { font-family: "Oswald", sans-serif; font-weight: 300; font-size: 88px; letter-spacing: 1px; }
  .headline .name { font-size: 106px; }
  .headline .mid { font-size: 106px; }
  .headline .end { font-size: 160px; margin-top: 8px; }
  .headline .row { display: flex; justify-content: flex-end; align-items: baseline; gap: 18px; }

  .contact { position: absolute; left: 32px; top: 1058px; }
  .phone {
    font-family: "Bebas Neue", sans-serif; font-size: 74px; line-height: 1;
    color: var(--phone); letter-spacing: 1px;
  }
  .website {
    margin-top: 12px;
    font-family: "Oswald", sans-serif; font-weight: 600; font-size: 34px; line-height: 1;
    color: var(--ink);
  }

  .services { position: absolute; left: 670px; top: 852px; color: var(--white); font-family: "Bebas Neue", sans-serif; }
  .services h2 { font-weight: 400; font-size: 70px; line-height: 1; letter-spacing: 1px; }
  .services ul { list-style: none; margin-top: 14px; }
  .services li { font-size: 44px; line-height: 41px; letter-spacing: 1px; display: flex; align-items: center; }
  .services li::before {
    content: ""; width: 13px; height: 13px; border-radius: 50%;
    background: var(--white); margin: 0 16px 0 8px; flex: none;
  }
</style>
</head>
<body>
<div class="billboard">
  <svg class="shapes" width="1040" height="1200" viewBox="0 0 1040 1200">
    <defs>
      <linearGradient id="bracketFill" x1="0" y1="0" x2="0" y2="1">
        <stop offset="0" stop-color="var(--bracket-top)"/>
        <stop offset="1" stop-color="var(--bracket-bottom)"/>
      </linearGradient>
      <linearGradient id="photoTone" x1="0" y1="0" x2="1" y2="1">
        <stop offset="0" stop-color="var(--photo-brick)"/>
        <stop offset="0.55" stop-color="#a35a48"/>
        <stop offset="0.8" stop-color="var(--photo-debris)"/>
        <stop offset="1" stop-color="#6f8a4a"/>
      </linearGradient>
    </defs>
    <path class="headline-band" d="M410 0H1040V400H630V225H410Z" fill="var(--navy)"/>
    <rect class="bracket-panel" x="410" y="245" width="201" height="779" fill="url(#bracketFill)"/>
    <path class="project-photo" role="img" aria-label="Photo of a brick house mid partial demolition with a pile of timber and debris in the yard under a flowering tree"
          d="M0 245H410V293H564V978H410V1024H0Z" fill="url(#photoTone)"/>
    <rect class="bar" x="611" y="437" width="291" height="48" fill="var(--bar)"/>
    <rect class="bar" x="611" y="595" width="429" height="47" fill="var(--bar)"/>
    <rect class="bar" x="611" y="750" width="291" height="47" fill="var(--bar)"/>
    <path class="services-band" d="M630 831H1040V1200H410V1043H630Z" fill="var(--blue)"/>
  </svg>

  <div class="brand"><span class="brand-mark"></span>KESSEL</div>

  <h1 class="headline">
    <span class="line row"><span class="lead">WATCH</span><span class="name">KESSEL</span></span>
    <span class="line mid">CLEAR THE</span>
    <span class="line end">LOT</span>
  </h1>

  <div class="contact">
    <div class="phone">(555) 201-4870</div>
    <div class="website">www.kesseldemo.com</div>
  </div>

  <section class="services">
    <h2>OUR SERVICES</h2>
    <ul>
      <li>ROOM GUT OUT</li>
      <li>HOUSE GUT OUT</li>
      <li>PARTIAL DEMOLITION</li>
      <li>FULL DEMOLITION</li>
      <li>COMMERCIAL</li>
      <li>RESIDENTIAL</li>
    </ul>
  </section>
</div>
</body>
</html>
```